Marlowby Services Website Design

We have most content but require a professional design. We have a logo already and will need it utilized along with several of the photos from the attached documentation.
First page should have our mission and Vision and the synapsis provided in the word document. Visitors will be prompted to select from one of our 3 divisions from this page.
Each division will have the same list of tabs : About, Services, Safety, Careers and Contact.
Photos on each divisions page should be representative of the divisions offerings. The word doc attached contains the requested content and we are open to edits that would complement and fill the website.
I like the Quorvane site www.quorvane.example - they are our competition so cant be modeled directly after this.
Please include prompts to request quote at each service page. align the format of the geotechnical page to the other 2 divisions.
I used chat gpt for some of the content so will need it optimized for SCO.

```html
<!DOCTYPE html>
<html lang="en">
<head>
<meta charset="utf-8">
<title>Marlowby Services</title>
<link href="https://fonts.googleapis.com/css2?family=Russo+One&family=Lato:wght@400;700&display=swap" rel="stylesheet">
<style>
:root{
  --red:#ec1c24;
  --red-band:#e8262c;
  --ink:#111111;
  --text:#333333;
  --light:#f5f5f5;
  --white:#ffffff;
  --black:#000000;
}
*{margin:0;padding:0;box-sizing:border-box}
html,body{width:1200px;height:2646px;overflow:hidden}
body{position:relative;font-family:"Lato",sans-serif;color:var(--text);background:var(--white)}
.abs{position:absolute}
.display{font-family:"Russo One",sans-serif;text-transform:uppercase}

.topbar{left:0;top:0;width:1200px;height:47px;background:var(--red);color:var(--white);font-size:15px}
.topbar .item{position:absolute;top:13px;display:flex;align-items:center;gap:8px}
.topbar .quote{font-family:"Russo One",sans-serif;font-size:15px}

.nav{left:0;top:47px;width:1200px;height:78px;background:var(--white);border-bottom:1px solid #222}
.brand{font-family:"Lato",sans-serif;font-weight:700;color:var(--red);text-transform:uppercase;letter-spacing:3px}
.nav .brand{position:absolute;left:111px;top:16px;font-size:38px}
.nav ul{position:absolute;right:157px;top:33px;display:flex;gap:46px;list-style:none;font-size:16px;color:var(--ink)}

.hero{left:0;top:125px;width:1200px;height:586px;background:linear-gradient(160deg,#4a4d50,#2d3236 50%,#3a3a36)}
.hero-text{left:0;top:248px;width:1200px;text-align:center;color:var(--white)}
.hero-text .welcome{font-size:33px;letter-spacing:1px;line-height:40px}
.hero-text .big{font-family:"Lato",sans-serif;font-weight:700;font-size:92px;color:var(--red);letter-spacing:10px;line-height:1;margin-top:4px}
.hero-text .lead{font-family:"Russo One",sans-serif;font-size:21px;line-height:28px;width:780px;margin:18px auto 0}
.btn{display:inline-block;font-family:"Russo One",sans-serif;text-transform:uppercase;font-size:16px;border-radius:24px 0 24px 0}
.btn-red{background:var(--red);color:var(--white)}
.btn-white{background:var(--white);color:var(--red)}
.hero .btn{position:absolute;left:500px;top:388px;width:189px;height:50px;line-height:50px;text-align:center;border-radius:24px}

.vision{left:0;top:711px;width:1200px;height:451px;background:var(--light)}
.vision-copy{left:115px;top:884px;width:405px;font-size:16px;line-height:26px}
.frame{border:2px solid var(--red);border-radius:18px}
.photo{border-radius:18px}

.mission-strip{left:0;top:1350px;width:1200px;height:34px;background:#e9e9ea}
.mission{left:0;top:1383px;width:1200px;height:628px;background:var(--red-band)}
.mission-copy{left:550px;top:1506px;width:545px;font-size:16px;line-height:25.7px;color:var(--white)}

.division{width:309px;height:228px;border-radius:18px;overflow:hidden}
.division .inner{position:absolute;left:16px;top:16px;right:16px;bottom:16px;border:3px solid var(--white);border-radius:16px;display:flex;align-items:center;justify-content:center;text-align:center;color:var(--white);font-family:"Russo One",sans-serif;font-size:22px;line-height:26px;text-transform:uppercase}

.footer{left:0;top:2258px;width:1200px;height:388px;background:var(--black);color:var(--white)}
.footer .brand{position:absolute;left:113px;top:80px;font-size:32px}
.footer h3{position:absolute;top:88px;font-family:"Russo One",sans-serif;font-size:19px;font-weight:400;text-transform:uppercase}
.footer ul{position:absolute;list-style:none;font-size:16px;line-height:30px}
.social{position:absolute;left:143px;top:147px;width:180px;display:flex;justify-content:center;gap:9px;font-size:11px;font-weight:700;color:var(--red)}
.email-field{position:absolute;left:723px;top:128px;width:245px;height:32px;border-bottom:1px solid #444;border-left:2px solid #ddd;padding-left:12px;font-size:15px;color:#777;line-height:32px}
.footer .btn{position:absolute;left:723px;top:182px;width:147px;height:41px;line-height:41px;text-align:center;font-size:15px}
.footer .rule{position:absolute;left:108px;top:310px;width:977px;height:1px;background:#333}
.footer .copy{position:absolute;left:0;top:340px;width:1200px;text-align:center;font-size:16px}
</style>
</head>
<body>

<header class="abs topbar">
  <div class="item" style="left:113px">
    <svg width="15" height="12" viewBox="0 0 15 12"><rect x="0.5" y="0.5" width="14" height="11" fill="#fff"/><path d="M1 1l6.5 5.5L14 1" stroke="#ec1c24" stroke-width="1.4" fill="none"/></svg>
    info@marlowby.example
  </div>
  <div class="item" style="left:773px">
    <svg width="15" height="15" viewBox="0 0 24 24"><path fill="#fff" d="M6.6 10.8a15.1 15.1 0 006.6 6.6l2.2-2.2a1 1 0 011-.25 11.4 11.4 0 003.6.57 1 1 0 011 1V20a1 1 0 01-1 1A17 17 0 013 4a1 1 0 011-1h3.5a1 1 0 011 1c0 1.25.2 2.45.57 3.57a1 1 0 01-.25 1z"/></svg>
    +1 555 010 0188
  </div>
  <div class="item quote" style="left:968px">
    <svg width="11" height="14" viewBox="0 0 11 14"><path fill="#fff" d="M0 0h7l4 4v10H0z"/><path stroke="#ec1c24" stroke-width="1" d="M2 7h7M2 9h7M2 11h7"/></svg>
    Free Quote
  </div>
</header>

<nav class="abs nav">
  <div class="brand">Marlowby</div>
  <ul><li>About</li><li>Services</li><li>Safety</li><li>Careers</li><li>Contact</li></ul>
</nav>

<section class="abs hero" role="img" aria-label="Aerial photo of a small town with a boom lift truck raised in the foreground">
  <a class="btn btn-red">Get Started</a>
</section>
<div class="abs hero-text">
  <div class="display welcome">Welcome to</div>
  <div class="big">MARLOWBY</div>
  <p class="lead">Marlowby Services: Delivering safe, reliable aerial access and maintenance services to Oil &amp; Gas, Construction, Utility, Renewable energy industries</p>
</div>

<section class="abs vision"></section>
<h2 class="abs display" style="left:113px;top:828px;font-size:36px;font-weight:400;color:#000">Our Vision</h2>
<p class="abs vision-copy">To be the leading provider of aerial access, geotechnical drilling, and service solutions, setting the standard for excellence in safety, efficiency, and environmental stewardship.</p>
<a class="abs btn btn-red" style="left:112px;top:1010px;width:190px;height:50px;line-height:50px;text-align:center">Learn More</a>
<div class="abs frame" style="left:638px;top:830px;width:367px;height:453px"></div>
<div class="abs photo" role="img" aria-label="Extended boom lift beside a white water tower under a blue sky" style="left:668px;top:783px;width:387px;height:470px;background:linear-gradient(180deg,#3f7fd6,#8ab8ec 60%,#7b8a68)"></div>

<div class="abs mission-strip"></div>
<section class="abs mission"></section>
<div class="abs frame" style="left:78px;top:1356px;width:368px;height:451px;border-color:#f06a6e"></div>
<div class="abs photo" role="img" aria-label="Top-down view of a white boom truck parked on a dirt lot" style="left:109px;top:1307px;width:387px;height:470px;background:linear-gradient(180deg,#a39468,#4f4a3e 45%,#3c3a35)"></div>
<h2 class="abs display" style="left:552px;top:1445px;font-size:36px;font-weight:400;color:#fff">Mission Statement</h2>
<p class="abs mission-copy">At Marlowby, our mission is to deliver unparalleled aerial access, geotechnical drilling, and service and maintenance solutions, consistently exceeding our clients' expectations. We strive to achieve this by investing in cutting-edge technology, fostering a culture of safety and continuous improvement, and prioritizing environmental sustainability. Through collaboration, integrity, and dedication, we aim to contribute to the success of our clients while maintaining the highest standards of quality and professionalism.</p>
<a class="abs btn btn-white" style="left:553px;top:1723px;width:169px;height:50px;line-height:50px;text-align:center">Learn More</a>

<div class="abs division" style="left:105px;top:1906px" role="img" aria-label="Aerial view of a town with a lift truck">
  <div class="abs" style="inset:0;background:linear-gradient(160deg,#6b7276,#3b4145)"></div>
  <div class="inner">Aerial Access</div>
</div>
<div class="abs division" style="left:443px;top:1906px" role="img" aria-label="Drilling rig and pickup truck on a grass lot from above">
  <div class="abs" style="inset:0;background:linear-gradient(160deg,#7a7d72,#5a6346)"></div>
  <div class="inner">Geotechnical<br>Drilling</div>
</div>
<div class="abs division" style="left:786px;top:1906px" role="img" aria-label="Boom lift working on a water tower">
  <div class="abs" style="inset:0;background:linear-gradient(180deg,#3d7bd0,#7aa8d8 70%,#6d7a5c)"></div>
  <div class="inner">Renewable<br>Energy Services</div>
</div>

<footer class="abs footer">
  <div class="brand">Marlowby</div>
  <div class="social"><span>Linkly</span><span>Pixo</span><span>Postr</span><span>Vidi</span></div>
  <h3 style="left:386px">Quick Links</h3>
  <ul style="left:389px;top:127px"><li>About</li><li>Services</li><li>Safety</li><li>Careers</li><li>Contact</li></ul>
  <h3 style="left:553px">Support</h3>
  <ul style="left:557px;top:129px"><li>Terms &amp; Conditions</li><li>Privacy Policy</li><li>About Us</li><li>Support</li></ul>
  <h3 style="left:723px">Subscribe to our Newsletter</h3>
  <div class="email-field">Enter Your Email</div>
  <a class="btn btn-red">Subscribe</a>
  <div class="rule"></div>
  <div class="copy">©Copyrights 2024 Marlowby &nbsp;| &nbsp; All Rights Reserved</div>
</footer>

</body>
</html>
```